Professional Package for CPA Firm

We would like a stationery design for our new CPA Firm based in Atlanta, GA called 'Vale 8'. We work with investors to help grow investments, tax free. We would like the design to have a professional/minimal look with a 'wow' factor. We need 9.5″ x 4.125″, 9x12, and 10x13 mailing envelopes, business cards, and a letterhead. We have a logo that is already complete. For the letterhead, we would like to have space to put credentials at the bottom of the page

Industry/Entity Type

CPA, Accounting

```html
<!DOCTYPE html>
<html lang="en">
<head>
<meta charset="utf-8">
<title>Vale 8 — Business Cards</title>
<link rel="stylesheet" href="https://fonts.googleapis.com/css2?family=Open+Sans:wght@400;600&display=swap">
<style>
  :root {
    --navy: #0f3552;
    --teal: #22b5bd;
    --sky: #2ab3e3;
    --coral: #f0575a;
    --white: #ffffff;
    --paper: #e7e9ec;
    --ink-soft: #dfe7ee;
  }
  * { box-sizing: border-box; margin: 0; padding: 0; }
  html, body { width: 1200px; height: 874px; overflow: hidden; }
  body {
    background: var(--paper);
    font-family: "Open Sans", sans-serif;
    position: relative;
  }
  .card {
    position: absolute;
    width: 620px;
    height: 354px;
    border-radius: 18px;
    overflow: hidden;
    box-shadow: 0 10px 28px rgba(10, 30, 50, 0.22);
  }
  .card-front {
    left: 440px;
    top: 56px;
    background: var(--navy);
    display: flex;
    flex-direction: column;
    align-items: center;
    justify-content: center;
  }
  .front-name {
    font-size: 76px;
    font-weight: 600;
    color: var(--sky);
    letter-spacing: 2px;
    line-height: 1;
  }
  .front-tagline {
    margin-top: 10px;
    font-size: 17px;
    color: var(--sky);
    letter-spacing: 3px;
  }
  .card-back {
    left: 140px;
    top: 462px;
    background: var(--navy);
  }
  .back-shape { position: absolute; inset: 0; }
  .back-brand {
    position: absolute;
    left: 0;
    top: 0;
    width: 290px;
    height: 300px;
    display: flex;
    flex-direction: column;
    align-items: center;
    justify-content: center;
  }
  .back-name {
    font-size: 58px;
    font-weight: 600;
    color: var(--navy);
    letter-spacing: 2px;
    line-height: 1;
  }
  .back-tagline {
    margin-top: 10px;
    font-size: 13px;
    color: var(--navy);
    letter-spacing: 2.2px;
  }
  .contact {
    position: absolute;
    right: 36px;
    top: 82px;
    width: 240px;
    text-align: right;
    color: var(--ink-soft);
  }
  .contact-name {
    font-size: 21px;
    color: var(--teal);
    letter-spacing: 1px;
    text-transform: uppercase;
    line-height: 1.1;
  }
  .contact-role {
    font-size: 15px;
    color: var(--coral);
    margin-bottom: 10px;
  }
  .contact-address {
    font-size: 15px;
    line-height: 1.35;
    margin-bottom: 10px;
  }
  .contact-list { list-style: none; }
  .contact-list li {
    font-size: 15px;
    line-height: 1.45;
    display: flex;
    justify-content: flex-end;
    align-items: center;
    gap: 10px;
  }
  .contact-icon { width: 12px; height: 12px; flex: none; }
</style>
</head>
<body>

  <section class="card card-front" aria-label="Business card front">
    <div class="front-name">Vale 8</div>
    <div class="front-tagline">CPAs and Tax Advisors</div>
  </section>

  <section class="card card-back" aria-label="Business card back">
    <svg class="back-shape" viewBox="0 0 620 354" width="620" height="354" aria-hidden="true">
      <path d="M0,0 H324 V205 Q324,232 308,256 L262,354 H0 Z" fill="var(--coral)"/>
      <path d="M0,0 H314 V203 Q314,229 298,252 L250,354 H0 Z" fill="var(--teal)"/>
      <path d="M0,0 H304 V200 Q304,226 288,248 L238,354 H0 Z" fill="var(--white)"/>
    </svg>

    <div class="back-brand">
      <div class="back-name">Vale 8</div>
      <div class="back-tagline">CPAs and Tax Advisors</div>
    </div>

    <div class="contact">
      <div class="contact-name">Daniel Hart</div>
      <div class="contact-role">President</div>
      <div class="contact-address">412 Juniper Court<br>Marietta, Georgia 30060</div>
      <ul class="contact-list">
        <li>555-214-7730
          <svg class="contact-icon" viewBox="0 0 16 16" aria-hidden="true"><path fill="var(--coral)" d="M3.6 1.2l2.3 2.6-1.3 2a9 9 0 0 0 5.6 5.6l2-1.3 2.6 2.3-1.4 2.2C7.6 16.5-.5 8.4.4 2.6z"/></svg>
        </li>
        <li>555-318-6042
          <svg class="contact-icon" viewBox="0 0 16 16" aria-hidden="true"><rect x="4" y="1" width="8" height="14" rx="1.5" fill="none" stroke="var(--coral)" stroke-width="1.6"/><circle cx="8" cy="12.3" r="1" fill="var(--coral)"/></svg>
        </li>
        <li>info@vale8.com
          <svg class="contact-icon" viewBox="0 0 16 16" aria-hidden="true"><rect x="1" y="3" width="14" height="10" rx="1" fill="var(--coral)"/><path d="M1.5 3.8L8 9l6.5-5.2" fill="none" stroke="var(--navy)" stroke-width="1.2"/></svg>
        </li>
        <li>www.vale8.com
          <svg class="contact-icon" viewBox="0 0 16 16" aria-hidden="true"><circle cx="8" cy="8" r="7" fill="var(--coral)"/><path d="M1 8h14M8 1c-3 3.5-3 10.5 0 14M8 1c3 3.5 3 10.5 0 14" fill="none" stroke="var(--navy)" stroke-width="1"/></svg>
        </li>
      </ul>
    </div>
  </section>

</body>
</html>
```